Stylish Business Cards Wanted

- DOUBLE SIDED Design Required -

High end, edgy cards for a corporate and personal stylist. Must include logo,
Name: Belinda Harwick
Title: Director and Stylist
telephone : +61 8 7142 5809
email: belinda@theloombriefing.example
website: theloombriefing.example
Tag: Corporate Workwear & Uniform Specialist | Personal Stylist
Would like nice icons for telephone, email, website

Target Market(s)

Businesses wanting stylish uniforms, people wanting stylish wardrobes

Industry/Entity Type

Corporate Workwear Stylist

Contact Information for Business Card

I would like black, white and gold foiling incorporated in the design - possibly a touch of the other colours on my branding guide attached Name: Belinda Harwick Title: Director and Stylist telephone : +61 8 7142 5809 email: belinda@theloombriefing.example website: theloombriefing.example Tag: Corporate Workwear & Uniform Specialist | Personal Stylist Would like nice icons for telephone, email, website

Font styles to use
Other font styles liked:
• Raleway

Colors

Designer to choose colors to be used in the design.

Requirements
Must have
• Gold foil accents

```html
<!DOCTYPE html>
<html lang="en">
<head>
<meta charset="utf-8">
<title>The Loom Briefing – Business Cards</title>
<link rel="stylesheet" href="https://fonts.googleapis.com/css2?family=Raleway:wght@500;600;700&family=Montserrat:wght@500&family=Arimo:wght@400&display=swap">
<style>
  :root {
    --backdrop: #dedede;
    --card-black: #0b0b0b;
    --pattern-tone: #1c2020;
    --card-white: #ffffff;
    --gold: #e5b93c;
    --ink: #111111;
    --muted-ink: #333333;
  }
  * { margin: 0; padding: 0; box-sizing: border-box; }
  html, body {
    width: 1200px; height: 900px; overflow: hidden;
    background: var(--backdrop);
  }
  .canvas { position: relative; width: 1200px; height: 900px; }

  .card {
    position: absolute; left: 280px; width: 640px; height: 366px;
    overflow: hidden;
    box-shadow: 0 6px 14px rgba(0,0,0,0.22);
  }
  .card--back { top: 60px; background: var(--card-black); }
  .card--front { top: 474px; background: var(--card-white); }

  /* Back side */
  .brand-pattern {
    position: absolute; inset: 0;
    background: linear-gradient(160deg, var(--card-black) 0%, var(--pattern-tone) 55%, var(--card-black) 100%);
  }
  .back-wordmark {
    position: absolute; left: 430px; top: 238px;
    font-family: "Raleway", sans-serif; font-weight: 600;
    font-size: 24px; line-height: 1.05; color: var(--gold);
    letter-spacing: 0.5px;
  }

  /* Front side */
  .front-wordmark {
    position: absolute; left: 70px; top: 92px; width: 210px;
    font-family: "Raleway", sans-serif; font-weight: 700;
    font-size: 40px; line-height: 1.05; color: var(--ink);
    text-align: center;
  }
  .divider {
    position: absolute; left: 304px; top: 62px;
    width: 3px; height: 170px; background: var(--gold);
  }
  .identity { position: absolute; left: 344px; top: 62px; }
  .identity__name {
    font-family: "Raleway", sans-serif; font-weight: 700;
    font-size: 25px; color: var(--ink); line-height: 1.1;
  }
  .identity__title {
    font-family: "Arimo", sans-serif; font-size: 14px;
    color: var(--muted-ink); margin-top: 2px;
  }
  .contact-list {
    position: absolute; left: 344px; top: 142px; list-style: none;
    font-family: "Arimo", sans-serif; font-size: 15px; color: var(--ink);
  }
  .contact-list__item {
    display: flex; align-items: center; gap: 12px; height: 26px;
  }
  .contact-icon { width: 18px; height: 18px; flex: none; }

  .service-band {
    position: absolute; left: 0; right: 0; top: 282px; height: 58px;
  }
  .service-band__rule {
    position: absolute; left: 0; right: 0; height: 3px; background: var(--gold);
  }
  .service-band__rule--top { top: 0; }
  .service-band__rule--bottom { bottom: 0; }
  .service-band__strip {
    position: absolute; left: 0; right: 0; top: 9px; height: 38px;
    background: var(--card-black);
    display: flex; align-items: center; justify-content: center; gap: 12px;
    font-family: "Montserrat", sans-serif; font-weight: 500;
    font-size: 15px; letter-spacing: 0.4px; color: var(--gold);
    text-transform: uppercase;
  }
</style>
</head>
<body>
<main class="canvas">

  <section class="card card--back" aria-label="Card back">
    <div class="brand-pattern" role="img" aria-label="Repeating brand wordmark pattern in dark grey on black"></div>
    <p class="back-wordmark">The Loom<br>Briefing</p>
  </section>

  <section class="card card--front" aria-label="Card front">
    <p class="front-wordmark">The Loom Briefing</p>
    <div class="divider"></div>

    <div class="identity">
      <h1 class="identity__name">Belinda Harwick</h1>
      <p class="identity__title">Director and Stylist</p>
    </div>

    <ul class="contact-list">
      <li class="contact-list__item">
        <svg class="contact-icon" viewBox="0 0 18 18" aria-hidden="true">
          <circle cx="9" cy="9" r="9" fill="#111"/>
          <path d="M6 4.5l1.6 0 .7 2.2-1 .8c.5 1.1 1.3 1.9 2.4 2.4l.8-1 2.2.7v1.6c0 .5-.4.8-.9.8C8.4 12 6 9.6 5.2 5.4c0-.5.3-.9.8-.9z" fill="#e5b93c"/>
        </svg>
        <span>+61 8 7142 5809</span>
      </li>
      <li class="contact-list__item">
        <svg class="contact-icon" viewBox="0 0 18 18" aria-hidden="true">
          <circle cx="9" cy="9" r="9" fill="#111"/>
          <rect x="4.5" y="6" width="9" height="6" fill="none" stroke="#e5b93c" stroke-width="1.1"/>
          <path d="M4.5 6l4.5 3.4L13.5 6" fill="none" stroke="#e5b93c" stroke-width="1.1"/>
        </svg>
        <span>belinda@theloombriefing.example</span>
      </li>
      <li class="contact-list__item">
        <svg class="contact-icon" viewBox="0 0 18 18" aria-hidden="true">
          <circle cx="9" cy="9" r="9" fill="#111"/>
          <circle cx="9" cy="9" r="4.3" fill="none" stroke="#e5b93c" stroke-width="1"/>
          <ellipse cx="9" cy="9" rx="1.9" ry="4.3" fill="none" stroke="#e5b93c" stroke-width="0.9"/>
          <path d="M4.7 9h8.6" stroke="#e5b93c" stroke-width="0.9"/>
        </svg>
        <span>theloombriefing.example</span>
      </li>
    </ul>

    <div class="service-band">
      <div class="service-band__rule service-band__rule--top"></div>
      <div class="service-band__strip">
        <span>Corporate Workwear</span><span>|</span>
        <span>Uniform Specialist</span><span>|</span>
        <span>Personal Stylist</span>
      </div>
      <div class="service-band__rule service-band__rule--bottom"></div>
    </div>
  </section>

</main>
</body>
</html>
```